Mortgage and Asset Finance Broker Needs a Wordpress Website Design

I need a modern looking Wordpress website to showcase my service as a mortgage and asset broker. I have a company and we work with various lenders to arrange mortgages, as well as commercial lending and business asset finance. The website needs to look professional, be easy to navigate and capture leads. SEO is obviously very important to me. It really needs to be something that shows trust and professioanlism.
Updates

On the home page I will need to have some boxes for Home Loans, Refinancing, Business (and Agriculture) Loans etc. I'd like a carousel in the middle which shows our lenders (so that can have the banks logos added).

It needs to be easy top navigate and showcase all we do - Home Loans, Refinancing, Commercial Loans, Car Loans, Asset Finance etc.

There are plenty of companies on the internet that do this.

There is some good information here https://lendplatehq.com.au/mortgage-broker-homepage/

I need to make sure that editing the website is easy (I think Wordpress has something that allows that).

Also we are very much an Australian business so that is something to advertise.

Industry/Entity Type

Mortgage and Finance Broker

Coding

Coded - Design and coding required

Number of Pages Required

5+ page

Requirements
Must have
• Easy to navigate professional feel. Must be responsive and mobile friendly.
Nice to have
• Homepage with links to inner pages. Contact buttons.

```html
<!DOCTYPE html>
<html lang="en">
<head>
<meta charset="utf-8">
<title>Northvale Finance – Home Loans &amp; Asset Finance</title>
<link href="https://fonts.googleapis.com/css2?family=Fira+Sans:wght@400;500;600;700&family=Roboto:wght@400;500;700&display=swap" rel="stylesheet">
<style>
:root{
  --pink:#d8075f;
  --pink-dark:#b8004f;
  --purple:#6b2c8e;
  --purple-dark:#4e1d6d;
  --blue:#17469e;
  --blue-dark:#0f3a8a;
  --ink:#1b1b1b;
  --body:#555;
  --muted:#8a8a8a;
  --footer:#131313;
  --white:#fff;
  --field:#fff;
}
*{box-sizing:border-box;margin:0;padding:0}
html,body{width:1200px;height:4329px;overflow:hidden}
body{font-family:"Roboto",sans-serif;color:var(--ink);background:var(--white);position:relative}
h1,h2,h3,h4,.heading{font-family:"Fira Sans",sans-serif}
.abs{position:absolute}
section,header,footer{position:absolute;left:0;width:1200px}

/* header */
.site-header{top:0;height:98px;background:#fff}
.topbar{position:absolute;left:487px;top:0;width:713px;height:44px;background:var(--pink);clip-path:polygon(0 0,100% 0,100% 100%,32px 100%);display:flex;align-items:center;justify-content:flex-end;gap:40px;padding-right:112px;color:#fff;font-size:14px}
.topbar b{font-weight:700}
.topbar span{display:flex;align-items:center;gap:8px}
.brand{position:absolute;left:112px;top:20px;display:flex;align-items:center;gap:10px}
.brand-dot{width:34px;height:34px;border-radius:50%;background:var(--purple)}
.brand-name{font-family:"Fira Sans",sans-serif;font-weight:700;font-size:30px;color:#222;letter-spacing:-.5px}
.nav{position:absolute;right:110px;top:62px;display:flex;gap:36px;font-size:14px;color:#222;font-weight:500}
.nav .active{color:var(--pink)}

/* hero */
.hero{top:98px;height:616px}
.hero-media{position:absolute;inset:0;background:linear-gradient(100deg,#6f6660 0%,#a39a90 40%,#cfc8be 70%,#b9a58f 100%)}
.hero-shade{position:absolute;inset:0;background:linear-gradient(90deg,rgba(40,30,30,.55) 0%,rgba(40,30,30,.15) 55%,rgba(0,0,0,0) 100%)}
.hero-copy{position:absolute;left:109px;top:88px;color:#fff;width:520px}
.hero-kicker{font-family:"Fira Sans",sans-serif;font-size:29px;font-weight:500}
.hero-title{font-size:45px;font-weight:700;line-height:51px;margin-top:10px}
.hero-text{font-size:16px;line-height:27px;margin-top:14px;width:430px}
.btn{display:inline-flex;align-items:center;background:var(--pink);color:#fff;font-family:"Fira Sans",sans-serif;font-weight:600;font-size:15px;height:44px;padding:0 24px 0 16px;position:relative;text-transform:uppercase;clip-path:polygon(0 0,100% 0,calc(100% - 14px) 100%,0 100%)}
.btn-wrap{position:relative;display:inline-block}
.btn-wrap::after{content:"";position:absolute;right:-14px;top:0;width:6px;height:44px;background:var(--pink);transform:skewX(-20deg)}
.hero .btn-wrap{margin-top:20px}

/* service cards */
.cards{position:absolute;top:620px;left:106px;display:flex;gap:20px}
.card{width:182px;height:212px;background:#fff;border-radius:4px;box-shadow:0 6px 20px rgba(0,0,0,.12);padding:19px 22px}
.card-icon{width:68px;height:68px;border-radius:50%;display:flex;align-items:center;justify-content:center}
.card h3{font-size:16px;font-weight:600;margin-top:28px;text-transform:uppercase}
.card p{font-size:15px;color:var(--body);margin-top:12px}
.card svg.arrow{margin-top:18px}

/* about */
.about{top:900px;height:480px}
.dots{position:absolute;background-image:radial-gradient(circle,#555 1.3px,transparent 1.5px);background-size:12px 12px}
.about-media{position:absolute;left:116px;top:64px;width:450px;height:353px;background:linear-gradient(135deg,#e7e3dc,#b9b3aa 60%,#8d7a68)}
.section-title{font-size:31px;font-weight:700;text-transform:uppercase}
.rule{height:4px;width:70px;background:var(--pink);margin-top:12px}
.about-copy{position:absolute;left:637px;top:63px;width:470px}
.about-copy p{font-size:14px;line-height:26px;color:var(--body);margin-top:22px}
.about-copy .btn-wrap{margin-top:22px}

/* services band */
.services{top:1431px;height:600px}
.services-band{position:absolute;left:0;top:0;width:1200px;height:476px;background:linear-gradient(90deg,var(--purple-dark),var(--purple) 50%,var(--purple-dark))}
.services .section-title{position:absolute;top:70px;width:100%;text-align:center;color:#fff;font-size:32px;font-weight:600}
.services .rule{position:absolute;top:124px;left:560px;width:80px;background:#fff;margin:0;height:3px}
.svc{position:absolute;top:169px;width:312px}
.svc-media{height:307px}
.svc h3{text-align:center;font-size:19px;font-weight:600;margin-top:27px;text-transform:uppercase}
.circle-btn{position:absolute;width:34px;height:34px;border-radius:50%;border:1.5px solid #fff;display:flex;align-items:center;justify-content:center;color:#fff}

/* fast track */
.fast{top:2031px;height:500px}
.fast h2{position:absolute;left:113px;top:40px;font-size:31px;font-weight:600;line-height:40px;text-transform:uppercase}
.fast ul{position:absolute;left:110px;top:157px;list-style:none;width:420px}
.fast li{display:flex;gap:10px;font-size:15px;line-height:30px;color:var(--body);margin-bottom:14px}
.fast li svg{flex:none;margin-top:8px}
.fast .btn-wrap{position:absolute;left:110px;top:383px}
.fast-media-a{position:absolute;left:719px;top:47px;width:341px;height:321px;background:linear-gradient(135deg,#7d8a8f,#3a4347 70%,#2b2f33)}
.fast-media-b{position:absolute;left:630px;top:240px;width:222px;height:187px;background:linear-gradient(135deg,#c9b49b,#8f7d6d 60%,#cfd3d8);border:4px solid #fff}

/* testimonials */
.testimonials{top:2574px;height:628px;background:linear-gradient(135deg,var(--blue-dark),var(--blue) 50%,var(--blue-dark))}
.testimonials .section-title{position:absolute;top:92px;width:100%;text-align:center;color:#fff;font-size:30px;font-weight:600}
.tcard{position:absolute;top:193px;width:308px;height:328px;border:2px solid #fff;border-radius:8px;padding:24px 24px 0;color:#fff}
.stars{color:#f7a21b;font-size:14px;letter-spacing:2px}
.tcard p{font-size:13.5px;line-height:26px;margin-top:12px;text-align:justify}
.tcard hr{border:0;border-top:1px solid rgba(255,255,255,.5);margin-top:40px}
.person{display:flex;align-items:center;gap:14px;margin-top:24px}
.avatar{width:56px;height:56px;border-radius:50%;background:linear-gradient(135deg,#c9a98a,#6a5646)}
.person b{font-family:"Fira Sans",sans-serif;font-size:18px;display:block}
.person span{font-size:14px;opacity:.9}
.circle-btn.white{background:#fff;color:var(--blue)}

/* lenders */
.lenders{top:3250px;height:120px;display:flex;justify-content:center;align-items:center;gap:78px}
.lender{width:100px;height:56px;border-radius:6px;background:#e4e4e4}
.lender.round{width:60px;height:60px;border-radius:50%}

/* contact */
.contact{top:3400px;height:460px}
.contact .section-title{position:absolute;top:36px;width:100%;text-align:center;font-size:30px;font-weight:700}
.field{position:absolute;background:var(--field);border-radius:4px;box-shadow:0 3px 12px rgba(0,0,0,.12);font-size:14px;color:#666;padding:14px 17px}
.contact .btn-wrap{position:absolute;left:529px;top:368px}

/* footer */
.site-footer{top:3919px;height:410px;background:var(--footer);color:#fff}
.footer-brand{position:absolute;left:114px;top:92px;display:flex;align-items:center;gap:12px}
.footer-brand .brand-name{color:#fff;font-size:40px}
.footer-brand .brand-dot{width:44px;height:44px}
.fcol{position:absolute;top:76px}
.fcol h4{font-size:21px;font-weight:500}
.fcol ul{list-style:none;margin-top:12px}
.fcol li{font-size:14.5px;line-height:31px;display:flex;align-items:center;gap:12px}
.contact-row{display:flex;align-items:center;gap:15px;font-size:14.5px;margin-top:22px}
.contact-row:first-of-type{margin-top:20px}
.ci{width:36px;height:36px;border-radius:50%;background:var(--blue);display:flex;align-items:center;justify-content:center}
.footer-rule{position:absolute;left:99px;top:336px;width:1002px;border-top:1px solid #444}
.copyright{position:absolute;top:360px;width:100%;text-align:center;font-size:14px}
</style>
</head>
<body>

<header class="site-header">
  <div class="topbar">
    <span><svg width="14" height="14" viewBox="0 0 24 24" fill="#fff"><path d="M6.6 10.8a15 15 0 0 0 6.6 6.6l2.2-2.2c.3-.3.7-.4 1-.2 1.1.4 2.3.6 3.6.6.6 0 1 .4 1 1V20c0 .6-.4 1-1 1A17 17 0 0 1 3 4c0-.6.4-1 1-1h3.5c.6 0 1 .4 1 1 0 1.3.2 2.5.6 3.6.1.3 0 .7-.2 1z"/></svg><b>Phone:</b> +1 555 0100 2200</span>
    <span><svg width="14" height="14" viewBox="0 0 24 24" fill="#fff"><path d="M2 5h20v14H2z" opacity=".0"/><path d="M2 5h20v14H2V5zm2 2v.5l8 5 8-5V7H4z"/></svg><b>Email:</b> info@northvalefinance.com</span>
  </div>
  <div class="brand"><span class="brand-dot"></span><span class="brand-name">Northvale Finance</span></div>
  <nav class="nav">
    <span class="active">HOME</span><span>ABOUT US</span><span>HOME LOANS</span><span>SERVICES</span><span>PARTNERS</span><span>BLOG</span><span>CONTACT US</span>
  </nav>
</header>

<section class="hero">
  <div class="hero-media" role="img" aria-label="Family sitting among moving boxes in front of a brick wall"></div>
  <div class="hero-shade"></div>
  <div class="hero-copy">
    <div class="hero-kicker">Welcome To</div>
    <h1 class="hero-title">Compare &amp; Save – Get the Best Home Loan Deals Now!</h1>
    <p class="hero-text">Excepteur sint occaecat cupidatat non proident, sunt in culpa qui officia deserunt mollit anim id est laborum.</p>
    <span class="btn-wrap"><span class="btn">Get Started</span></span>
  </div>
</section>

<div class="cards">
  <div class="card"><div class="card-icon" style="background:#174ea6"><svg width="34" height="34" viewBox="0 0 24 24" fill="none" stroke="#fff" stroke-width="1.6"><path d="M3 11l9-7 9 7M5 10v10h14V10M10 20v-6h4v6"/></svg></div><h3>Home Loans</h3><p>Lorem ipsum dolor</p><svg class="arrow" width="22" height="14" viewBox="0 0 22 14" fill="none" stroke="#222" stroke-width="1.6"><path d="M1 7h19M14 1l6 6-6 6"/></svg></div>
  <div class="card"><div class="card-icon" style="background:var(--pink)"><svg width="34" height="34" viewBox="0 0 24 24" fill="none" stroke="#fff" stroke-width="1.6"><path d="M4 12a8 8 0 0 1 14-5M20 12a8 8 0 0 1-14 5M18 3v4h-4M6 21v-4h4"/></svg></div><h3>Refinancing</h3><p>Lorem ipsum dolor</p><svg class="arrow" width="22" height="14" viewBox="0 0 22 14" fill="none" stroke="#222" stroke-width="1.6"><path d="M1 7h19M14 1l6 6-6 6"/></svg></div>
  <div class="card"><div class="card-icon" style="background:#f07a1a"><svg width="34" height="34" viewBox="0 0 24 24" fill="none" stroke="#fff" stroke-width="1.6"><path d="M4 21V8l8-4 8 4v13M9 21v-5h6v5M8 11h2M14 11h2"/></svg></div><h3>Commercial</h3><p>Lorem ipsum dolor</p><svg class="arrow" width="22" height="14" viewBox="0 0 22 14" fill="none" stroke="#222" stroke-width="1.6"><path d="M1 7h19M14 1l6 6-6 6"/></svg></div>
  <div class="card"><div class="card-icon" style="background:#5b2a86"><svg width="34" height="34" viewBox="0 0 24 24" fill="none" stroke="#fff" stroke-width="1.6"><path d="M3 16v-4l2-5h14l2 5v4zM3 16v3h3v-3M18 16v3h3v-3M7 13h1M16 13h1"/></svg></div><h3>Car Loans</h3><p>Lorem ipsum dolor</p><svg class="arrow" width="22" height="14" viewBox="0 0 22 14" fill="none" stroke="#222" stroke-width="1.6"><path d="M1 7h19M14 1l6 6-6 6"/></svg></div>
  <div class="card"><div class="card-icon" style="background:var(--pink)"><svg width="34" height="34" viewBox="0 0 24 24" fill="none" stroke="#fff" stroke-width="1.6"><path d="M2 15h4l5 3 7-4M6 15V9h5l3 2M14 4h7v6h-7z"/></svg></div><h3>Asset Finance</h3><p>Lorem ipsum dolor</p><svg class="arrow" width="22" height="14" viewBox="0 0 22 14" fill="none" stroke="#222" stroke-width="1.6"><path d="M1 7h19M14 1l6 6-6 6"/></svg></div>
</div>

<section class="about">
  <div class="dots" style="left:380px;top:42px;width:180px;height:96px"></div>
  <div class="dots" style="left:126px;top:335px;width:180px;height:92px"></div>
  <div class="about-media" role="img" aria-label="Small model house beside wooden blocks with a percent sign"></div>
  <div class="about-copy">
    <h2 class="section-title">About Us</h2>
    <div class="rule"></div>
    <p>Lorem ipsum dolor sit amet, consectetur adipiscing elit, sed do eiusmod tempor incididunt ut labore et dolore magna aliqua. Ut enim ad minim veniam, quis nostrud exercitation ullamco laboris nisi ut aliquip ex ea commodo consequat. Duis aute irure dolor in reprehenderit in voluptate velit esse cillum dolore eu fugiat nulla pariatur. Excepteur sint occaecat cupidatat non proident, sunt in culpa qui officia deserunt mollit anim id est laborum.Ut enim ad&nbsp; suscipit laboriosam, nisi ut aliquid ex ea commodi consequatur?</p>
    <span class="btn-wrap"><span class="btn">Read More</span></span>
  </div>
</section>

<section class="services">
  <div class="services-band"></div>
  <h2 class="section-title">Our Services</h2>
  <div class="rule"></div>
  <div class="svc" style="left:109px"><div class="svc-media" role="img" aria-label="Model house on a desk during a loan signing" style="background:linear-gradient(135deg,#d9d2c6,#9b8a74 60%,#5f5547)"></div><h3>Home Loans</h3></div>
  <div class="svc" style="left:444px"><div class="svc-media" role="img" aria-label="Jar of coins beside a small white model house" style="background:linear-gradient(135deg,#c4a886,#8c6b4e 60%,#e6ded4)"></div><h3>Refinancing</h3></div>
  <div class="svc" style="left:778px"><div class="svc-media" role="img" aria-label="Business clients meeting at a glass table" style="background:linear-gradient(135deg,#a9b3b8,#6e6a5e 55%,#cfd4d6)"></div><h3>Business Loans</h3></div>
  <div class="circle-btn" style="left:37px;top:291px"><svg width="10" height="14" viewBox="0 0 10 14" fill="none" stroke="#fff" stroke-width="1.8"><path d="M8 1L2 7l6 6"/></svg></div>
  <div class="circle-btn" style="left:1129px;top:291px"><svg width="10" height="14" viewBox="0 0 10 14" fill="none" stroke="#fff" stroke-width="1.8"><path d="M2 1l6 6-6 6"/></svg></div>
</section>

<section class="fast">
  <h2>How We Fast-Track Your<br>Home Loan Approval</h2>
  <ul>
    <li><svg width="16" height="16" viewBox="0 0 16 16"><circle cx="8" cy="8" r="8" fill="var(--purple)"/><path d="M4.5 8.2l2.3 2.3 4.7-4.7" stroke="#fff" stroke-width="1.8" fill="none"/></svg><span>Excepteur sint occaecat cupidatat non proident, sunt in culpa qui officia deserunt mollit anim id est laborum.</span></li>
    <li><svg width="16" height="16" viewBox="0 0 16 16"><circle cx="8" cy="8" r="8" fill="var(--purple)"/><path d="M4.5 8.2l2.3 2.3 4.7-4.7" stroke="#fff" stroke-width="1.8" fill="none"/></svg><span>Duis aute irure dolor in reprehenderit in voluptate velit esse cillum dolore eu fugiat nulla pariatur.</span></li>
    <li><svg width="16" height="16" viewBox="0 0 16 16"><circle cx="8" cy="8" r="8" fill="var(--purple)"/><path d="M4.5 8.2l2.3 2.3 4.7-4.7" stroke="#fff" stroke-width="1.8" fill="none"/></svg><span>Excepteur sint occaecat cupidatat non proident, sunt in culpa qui officia deserunt mollit anim id est laborum.</span></li>
  </ul>
  <span class="btn-wrap"><span class="btn">Read More</span></span>
  <div class="dots" style="left:662px;top:104px;width:54px;height:100px"></div>
  <div class="dots" style="left:892px;top:372px;width:108px;height:42px"></div>
  <div class="fast-media-a" role="img" aria-label="Advisers meeting clients in a bright office"></div>
  <div class="fast-media-b" role="img" aria-label="Wooden model house on loan paperwork"></div>
</section>

<section class="testimonials">
  <h2 class="section-title">Client&nbsp; Testimonial</h2>
  <div class="tcard" style="left:109px"><div class="stars">★★★★★</div><p>Lorem ipsum dolor sit amet, consectetur adipiscing elit, sed do eiusmod tempor incididunt ut labore et dolore magna aliqua ut enim ad minim veniam, quis nostrud exercitation ullamco.</p><hr><div class="person"><div class="avatar" role="img" aria-label="Client portrait"></div><div><b>Liam Carter</b><span>Florida, United States</span></div></div></div>
  <div class="tcard" style="left:445px"><div class="stars">★★★★★</div><p>Lorem ipsum dolor sit amet, consectetur adipiscing elit, sed do eiusmod tempor incididunt ut labore et dolore magna aliqua ut enim ad minim veniam, quis nostrud exercitation ullamco.</p><hr><div class="person"><div class="avatar" role="img" aria-label="Client portrait"></div><div><b>Liam Carter</b><span>Florida, United States</span></div></div></div>
  <div class="tcard" style="left:781px"><div class="stars">★★★★★</div><p>Lorem ipsum dolor sit amet, consectetur adipiscing elit, sed do eiusmod tempor incididunt ut labore et dolore magna aliqua ut enim ad minim veniam, quis nostrud exercitation ullamco.</p><hr><div class="person"><div class="avatar" role="img" aria-label="Client portrait"></div><div><b>Liam Carter</b><span>Florida, United States</span></div></div></div>
  <div class="circle-btn" style="left:41px;top:357px"><svg width="10" height="14" viewBox="0 0 10 14" fill="none" stroke="#fff" stroke-width="1.8"><path d="M8 1L2 7l6 6"/></svg></div>
  <div class="circle-btn white" style="left:1132px;top:357px"><svg width="10" height="14" viewBox="0 0 10 14" fill="none" stroke="var(--blue)" stroke-width="1.8"><path d="M2 1l6 6-6 6"/></svg></div>
</section>

<section class="lenders" aria-label="Lender partners">
  <div class="lender"></div><div class="lender"></div><div class="lender"></div><div class="lender round"></div><div class="lender round"></div><div class="lender"></div>
</section>

<section class="contact">
  <h2 class="section-title">Contact Us</h2>
  <div class="field" style="left:181px;top:133px;width:411px;height:47px">Name</div>
  <div class="field" style="left:605px;top:133px;width:412px;height:47px">Email</div>
  <div class="field" style="left:181px;top:195px;width:411px;height:47px">Phone Number</div>
  <div class="field" style="left:605px;top:195px;width:412px;height:47px">Subject</div>
  <div class="field" style="left:181px;top:259px;width:836px;height:84px">Message</div>
  <span class="btn-wrap"><span class="btn">Submit Now</span></span>
</section>

<footer class="site-footer">
  <div class="footer-brand"><span class="brand-dot"></span><span class="brand-name">Northvale</span></div>
  <div class="fcol" style="left:427px"><h4>Quick Links</h4><ul>
    <li><svg width="12" height="12" viewBox="0 0 12 12" fill="#fff"><path d="M5 0l6 6-6 6V8H0V4h5z"/></svg>Home</li>
    <li><svg width="12" height="12" viewBox="0 0 12 12" fill="#fff"><path d="M5 0l6 6-6 6V8H0V4h5z"/></svg>About Us</li>
    <li><svg width="12" height="12" viewBox="0 0 12 12" fill="#fff"><path d="M5 0l6 6-6 6V8H0V4h5z"/></svg>Services</li>
    <li><svg width="12" height="12" viewBox="0 0 12 12" fill="#fff"><path d="M5 0l6 6-6 6V8H0V4h5z"/></svg>Partners</li>
    <li><svg width="12" height="12" viewBox="0 0 12 12" fill="#fff"><path d="M5 0l6 6-6 6V8H0V4h5z"/></svg>Blog</li>
    <li><svg width="12" height="12" viewBox="0 0 12 12" fill="#fff"><path d="M5 0l6 6-6 6V8H0V4h5z"/></svg>Contact us</li>
  </ul></div>
  <div class="fcol" style="left:642px"><h4>Other Links</h4><ul>
    <li><svg width="12" height="12" viewBox="0 0 12 12" fill="#fff"><path d="M5 0l6 6-6 6V8H0V4h5z"/></svg>FAQ</li>
    <li><svg width="12" height="12" viewBox="0 0 12 12" fill="#fff"><path d="M5 0l6 6-6 6V8H0V4h5z"/></svg>Terms of Use</li>
    <li><svg width="12" height="12" viewBox="0 0 12 12" fill="#fff"><path d="M5 0l6 6-6 6V8H0V4h5z"/></svg>Privacy Policy</li>
    <li><svg width="12" height="12" viewBox="0 0 12 12" fill="#fff"><path d="M5 0l6 6-6 6V8H0V4h5z"/></svg>Support Links</li>
    <li><svg width="12" height="12" viewBox="0 0 12 12" fill="#fff"><path d="M5 0l6 6-6 6V8H0V4h5z"/></svg>Conditions</li>
  </ul></div>
  <div class="fcol" style="left:845px"><h4>Contact Us</h4>
    <div class="contact-row"><span class="ci"><svg width="14" height="16" viewBox="0 0 24 24" fill="#fff"><path d="M12 2a7 7 0 0 0-7 7c0 5 7 13 7 13s7-8 7-13a7 7 0 0 0-7-7zm0 9.5A2.5 2.5 0 1 1 12 6.5a2.5 2.5 0 0 1 0 5z"/></svg></span>Northvale, Sydney NSW</div>
    <div class="contact-row"><span class="ci"><svg width="14" height="14" viewBox="0 0 24 24" fill="#fff"><path d="M2 5h20v14H2V5zm2 2v.5l8 5 8-5V7H4z"/></svg></span>info@northvale.com</div>
    <div class="contact-row"><span class="ci"><svg width="14" height="14" viewBox="0 0 24 24" fill="#fff"><path d="M6.6 10.8a15 15 0 0 0 6.6 6.6l2.2-2.2c.3-.3.7-.4 1-.2 1.1.4 2.3.6 3.6.6.6 0 1 .4 1 1V20c0 .6-.4 1-1 1A17 17 0 0 1 3 4c0-.6.4-1 1-1h3.5c.6 0 1 .4 1 1 0 1.3.2 2.5.6 3.6.1.3 0 .7-.2 1z"/></svg></span>+1 555 0100 2200</div>
  </div>
  <div class="footer-rule"></div>
  <div class="copyright">Copyrights@2025.Northvale.All Rights Reserved</div>
</footer>

</body>
</html>
```